Website for a Psychologist in Private Practice

I need a cool web design for my website: www.drkalvoric.com. I would like it to look professional. Keep all the current content and add: Space for video; radio spots (see Silver Cedar Tunes Logo below for those); Quick Inquiry; Friendora link; 5 star rating on Rivo; a map; reviews from former patients. I am open to suggestions.

Target Market(s)

Those seeking individual and marital counseling.

Industry/Entity Type

Mental Health

Number of Pages Required

1 page

Font styles to use
Sans Serif
Other font styles liked:
• I'm open but no hard to read script

Requirements
Must have
• All the content on my home page with link for video and radio spots. List services and degrees and expertices (pics not necessary).
Nice to have
• A video of me and radio conversations (logo of Silver Cedar Tunes radio attached).
Should not have
• Cartoons, comedy, etc.... I don't need pictures of services (marital, depression, etc...) Just list those.

```html
<!DOCTYPE html>
<html lang="en">
<head>
<meta charset="utf-8">
<title>Dr. Mara J. Kalvoric — Clinical Psychologist</title>
<link href="https://fonts.googleapis.com/css2?family=Lato:ital,wght@0,400;0,700;1,400&family=Roboto+Condensed:wght@400;700&family=Great+Vibes&display=swap" rel="stylesheet">
<style>
:root{
  --gold:#c9a74a;
  --gold-dark:#b8953a;
  --ink:#3a3a3a;
  --text:#555;
  --dark:#2b2b2b;
  --darker:#1c1c1c;
  --panel:#fbfbfb;
  --panel-alt:#f2f2f2;
  --sky:#e6eaeb;
}
*{margin:0;padding:0;box-sizing:border-box}
html,body{width:886px;height:1200px;overflow:hidden}
body{position:relative;font-family:'Lato',sans-serif;color:var(--text);background:linear-gradient(180deg,#dfe4e5 0%,#eef0f0 40%,#e4e8e9 80%);}
.abs{position:absolute}
.script{font-family:'Great Vibes',cursive;font-weight:400}
.script .accent{color:var(--gold)}

/* header */
.hero{left:0;top:0;width:886px;height:250px;background:radial-gradient(ellipse at 30% 55%,#8fb25a 0%,#5f8a34 40%,#3c6424 75%,#2f5119 100%)}
.hero-portrait{left:600px;top:0;width:286px;height:250px;background:radial-gradient(ellipse at 55% 40%,#e8c9a8 0%,#c9a47e 30%,#6f8fb0 70%,#3d5f88 100%)}
.brand-tab{left:0;top:0;width:415px;height:46px;background:linear-gradient(90deg,#f6f4ec,#fff);clip-path:polygon(0 0,100% 0,92% 100%,0 100%)}
.brand{left:119px;top:10px;font-size:22px;font-weight:700;color:var(--gold);letter-spacing:.3px}
.hero-title{left:119px;top:98px;font-family:'Roboto Condensed',sans-serif;font-weight:700;font-size:22px;line-height:27px;color:#fff}
.hero-sub{left:119px;top:160px;width:360px;font-size:10.5px;line-height:16px;color:#fff}

/* nav */
.nav{left:0;top:250px;width:886px;height:30px;background:var(--dark)}
.nav-links{left:119px;top:0;height:30px;display:flex;align-items:center;font-family:'Roboto Condensed',sans-serif;font-size:10px;color:#fff;letter-spacing:.3px}
.nav-links span{margin-right:22px}
.nav-links .active{color:var(--gold)}
.nav-contact{left:541px;top:250px;width:345px;height:30px;background:var(--gold);clip-path:polygon(8px 0,100% 0,100% 100%,18px 100%)}
.nav-edge{left:541px;top:250px;width:24px;height:30px}
.contact-item{top:259px;font-size:9px;color:var(--ink);display:flex;align-items:center;gap:6px}

/* content panel */
.panel{left:120px;top:280px;width:647px;height:717px;background:var(--panel);box-shadow:0 6px 10px rgba(0,0,0,.35)}
.h-section{font-size:22px;color:var(--ink)}
.about-title{left:136px;top:308px}
.about-text{left:136px;top:344px;width:614px;font-size:8.6px;line-height:13.3px}
.about-text p{margin-bottom:11px}
.about-text h3{font-size:11px;font-weight:700;color:var(--ink);margin:1px 0 4px}

.inquiry-band{left:120px;top:582px;width:647px;height:240px;background:var(--panel-alt)}
.inquiry-title{left:135px;top:603px}
.field{background:#fff;border:1px solid #e6e6e6;font-size:7.5px;color:#999;padding:6px 6px}
.btn-submit{left:135px;top:770px;width:50px;height:18px;background:var(--gold);border-radius:2px;color:#fff;font-size:8px;font-weight:700;display:flex;align-items:center;justify-content:center}
.divider{left:421px;top:620px;width:1px;height:180px;background:#ddd}
.video-title{left:453px;top:603px}
.video-frame{left:454px;top:638px;width:292px;height:166px;background:#fff;border:1px solid #ddd}
.video-still{left:458px;top:642px;width:283px;height:157px;background:radial-gradient(ellipse at 70% 45%,#dcbfa0 0%,#a78c6c 22%,#5a7f3a 50%,#35591d 100%)}
.video-label{left:466px;top:648px;font-size:11px;font-weight:700;color:#fff}
.video-bar{left:468px;top:773px;width:258px;height:18px;background:rgba(20,20,20,.75);border-radius:2px}

.radio-art{left:135px;top:853px;width:118px;height:117px;background:linear-gradient(150deg,#e84d87 0%,#c96b64 35%,#8a6b58 70%,#6d8c5c 100%)}
.radio-title{left:272px;top:848px}
.radio-text{left:272px;top:880px;width:475px;font-size:8.7px;line-height:13.5px;font-style:italic}
.radio-author{left:272px;top:939px;font-size:7.5px;color:var(--ink)}
.dots{left:272px;top:957px;display:flex;gap:4px}
.dots i{width:7px;height:7px;border-radius:50%;background:var(--dark);display:block}
.dots i:first-child{background:var(--gold)}

/* footer */
.footer{left:0;top:970px;width:886px;height:202px;background:var(--dark)}
.footer-bottom{left:0;top:1172px;width:886px;height:28px;background:var(--darker);color:#ddd;font-size:8.5px;display:flex;align-items:center;justify-content:center}
.f-head{font-size:11.5px;font-weight:700;color:#fff}
.f-head::after{content:"";display:block;width:18px;height:2px;background:#666;margin-top:5px}
.f-links{font-size:8px;color:#fff;line-height:20px;list-style:none}
.f-links li::before{content:"•";color:var(--gold);margin-right:5px}
.f-links .current{color:var(--gold)}
.f-contact{font-size:8px;color:#fff;line-height:12px}
.f-row{position:absolute;display:flex;gap:8px}
.map{left:438px;top:1043px;width:182px;height:109px;border:2px solid #fff;background:linear-gradient(135deg,#e9e7e1 0%,#dfe3dc 50%,#cfdfe8 100%)}
.social{width:22px;height:22px;border-radius:50%;display:block}
.donate{left:661px;top:1087px;font-size:8px;font-weight:700;color:#fff;line-height:10px}
.badge{top:1121px;width:49px;height:22px;background:#f4f4f4}
</style>
</head>
<body>

<div class="abs hero" role="img" aria-label="Soft green foliage backdrop"></div>
<div class="abs hero-portrait" role="img" aria-label="Portrait photo of the psychologist"></div>
<div class="abs brand-tab"></div>
<div class="abs brand">Dr. Mara J. Kalvoric</div>
<h1 class="abs hero-title">CLINICAL PSYCHOLOGIST California<br># PSY20581</h1>
<p class="abs hero-sub">Doctoral Degree in Clinical Psychology Masters Degree in Counseling Psychology Doctoral Internship, Coastview Medical Center &nbsp;Masters Internship, Linden Clinic</p>

<nav class="abs nav">
  <div class="abs nav-links">
    <span class="active">SESSIONS</span><span>|</span><span>RESOURCES</span><span>|</span><span>BIO</span><span>|</span><span>CONTACT US</span>
  </div>
</nav>
<div class="abs nav-contact"></div>
<svg class="abs nav-edge" viewBox="0 0 24 30"><line x1="8" y1="0" x2="18" y2="30" stroke="#1c1c1c" stroke-width="2"/></svg>
<div class="abs contact-item" style="left:578px">
  <svg width="11" height="11" viewBox="0 0 24 24"><path d="M6.6 10.8a15 15 0 006.6 6.6l2.2-2.2c.3-.3.7-.4 1-.2 1.1.4 2.3.6 3.6.6.6 0 1 .4 1 1V20c0 .6-.4 1-1 1A17 17 0 013 4c0-.6.4-1 1-1h3.5c.6 0 1 .4 1 1 0 1.3.2 2.5.6 3.6.1.3 0 .7-.2 1z" fill="none" stroke="#3a3a3a" stroke-width="2"/></svg>
  (555) 210 4832
</div>
<div class="abs contact-item" style="left:672px">
  <svg width="11" height="11" viewBox="0 0 24 24"><rect x="2" y="5" width="20" height="14" fill="none" stroke="#3a3a3a" stroke-width="2"/><path d="M2 5l10 8 10-8" fill="none" stroke="#3a3a3a" stroke-width="2"/></svg>
  mk@drkalvoric.com
</div>

<div class="abs footer"></div>
<div class="abs panel"></div>

<h2 class="abs h-section script about-title">About <span class="accent">Dr. Mara J. Kalvoric</span></h2>
<div class="abs about-text">
  <p>I'm so glad you are here. &nbsp;Choosing to see a professional for issues in your life can be difficult but also possibly life changing. &nbsp;Many postpone seeking help because they believe doing so acknowledges failure on their part. &nbsp;Reallly? &nbsp;We seek the help of experts all the time (contractors, mechanics, chefs, etc...) and what is more important than your life? Consulting with a neutral party to act in your best interest can be time well spent. &nbsp;So if you are willing to take the time to invest in counseling, make sure that it is with someone that is worth your time.</p>
  <p>Choose a licensed psychologist with a doctoral degree (Ph.D. or PsyD.) - both have over 10 years of education in the field of psychology, extensive internships and comprehensive licensing exams. &nbsp;Others have far less education if any. &nbsp;Also, consider tthe therapist's approach to therapy. &nbsp;I use a straightforward approach (psychobabble available upon request) with brief, solution-oriented sessions.</p>
  <p>Experience also separates good psychologists from others with fewer and more proficient sessions. My &nbsp;20+ years of professional experience and my life experience contributes to the empathetic perspective I use to relate to each person I see. &nbsp;I also believe it is the reason 90% of my practice is referral based and why many other psychologists in the area seek my services.</p>
  <h3>DO NOT COMPROMISE.</h3>
  <p>Find an educated, licensed, experienced professional that you can relate to. Think about what it took to get you here and the importance resolving this issue can have on your life.</p>
</div>

<div class="abs inquiry-band"></div>
<h2 class="abs h-section script inquiry-title">Quick <span class="accent">Inquiry</span></h2>
<div class="abs field" style="left:135px;top:642px;width:126px;height:21px">Full Name</div>
<div class="abs field" style="left:268px;top:642px;width:126px;height:21px">Phone No</div>
<div class="abs field" style="left:135px;top:672px;width:259px;height:21px">Email</div>
<div class="abs field" style="left:135px;top:701px;width:259px;height:55px">Message</div>
<div class="abs btn-submit">Submit</div>
<div class="abs divider"></div>

<h2 class="abs h-section script video-title">View <span class="accent">Video</span></h2>
<div class="abs video-frame"></div>
<div class="abs video-still" role="img" aria-label="Video still of the psychologist outdoors"></div>
<div class="abs video-label">Dr. Mara J. Kalvoric</div>
<div class="abs video-bar"></div>
<svg class="abs" style="left:468px;top:773px" width="258" height="18" viewBox="0 0 258 18">
  <rect x="0" y="0" width="34" height="18" fill="#333"/>
  <path d="M13 4l9 5-9 5z" fill="#fff"/>
  <rect x="42" y="3" width="22" height="7" fill="#222"/>
  <text x="44" y="9" font-size="5.5" fill="#fff" font-family="Lato,sans-serif">00:01</text>
  <rect x="42" y="11" width="144" height="4" fill="#555"/>
  <rect x="42" y="11" width="5" height="4" fill="#3cb3e0"/>
  <g fill="#3cb3e0"><rect x="194" y="6" width="2" height="8"/><rect x="197" y="6" width="2" height="8"/><rect x="200" y="6" width="2" height="8"/><rect x="203" y="6" width="2" height="8"/></g>
  <text x="212" y="13" font-size="9" font-weight="700" font-style="italic" fill="#ddd" font-family="Lato,sans-serif">HD</text>
  <path d="M236 5h4M236 5v4M246 13h-4M246 13v-4M246 5h-4M246 5v4M236 13h4M236 13v-4" stroke="#ddd" stroke-width="1.3"/>
</svg>

<div class="abs radio-art" role="img" aria-label="Silver Cedar Tunes radio show poster"></div>
<h2 class="abs h-section script radio-title">Radio <span class="accent">Conversations</span></h2>
<p class="abs radio-text">Lorem ipsum dolor sit amet, consectetur adipiscing elit, sed do eiusmod tempor incididunt ut labore et dolore magna aliqua. Ut enim ad minim veniam, quis nostrud exercitation ullamco laboris nisi ut aliquip ex ea commodo consequat. Duis aute irure dolor in reprehenderit in voluptate velit esse cillum dolore eu fugiat nulla pariatur. Excepteur sint occaecat cupidatat non proident, sunt in culpa qui officia deserunt mollit anim id est laborum. <span style="color:#bbb;font-size:14px">&rdquo;</span></p>
<div class="abs radio-author"><b>Mick,</b> Vantor Freight Ltd</div>
<div class="abs dots"><i></i><i></i><i></i><i></i></div>

<div class="abs f-head" style="left:130px;top:1016px">Quick Links</div>
<ul class="abs f-links" style="left:129px;top:1037px">
  <li class="current">Home</li><li>Sessions</li><li>Resources</li><li>Bio</li><li>Contact Us</li>
</ul>

<div class="abs f-head" style="left:251px;top:1016px">Contact Details</div>
<div class="f-row f-contact" style="left:251px;top:1042px">
  <svg width="9" height="12" viewBox="0 0 12 16"><path d="M6 0a6 6 0 00-6 6c0 4.5 6 10 6 10s6-5.5 6-10a6 6 0 00-6-6zm0 8.5A2.5 2.5 0 116 3.5a2.5 2.5 0 010 5z" fill="#fff"/></svg>
  <div><b>Dr. Mara J. Kalvoric</b><br>410 Harbor Lane #120<br>Seabrook, CA. 90412</div>
</div>
<div class="f-row f-contact" style="left:251px;top:1090px">
  <svg width="9" height="9" viewBox="0 0 24 24"><path d="M6.6 10.8a15 15 0 006.6 6.6l2.2-2.2c.3-.3.7-.4 1-.2 1.1.4 2.3.6 3.6.6.6 0 1 .4 1 1V20c0 .6-.4 1-1 1A17 17 0 013 4c0-.6.4-1 1-1h3.5c.6 0 1 .4 1 1 0 1.3.2 2.5.6 3.6.1.3 0 .7-.2 1z" fill="#fff"/></svg>
  (555) 210 4832
</div>
<div class="f-row f-contact" style="left:251px;top:1116px">
  <svg width="9" height="11" viewBox="0 0 10 14"><rect x="1" y="0.5" width="8" height="13" rx="1" fill="none" stroke="#fff"/><circle cx="5" cy="11.5" r=".8" fill="#fff"/></svg>
  (555) 210 4832
</div>
<div class="f-row f-contact" style="left:251px;top:1141px">
  <svg width="9" height="9" viewBox="0 0 24 24"><rect x="2" y="5" width="20" height="14" fill="#fff"/><path d="M2 5l10 8 10-8" fill="none" stroke="#2b2b2b" stroke-width="2"/></svg>
  mk@drkalvoric.com
</div>

<div class="abs f-head" style="left:438px;top:1016px">Location Map</div>
<div class="abs map" role="img" aria-label="Street map of the office location"></div>

<div class="abs f-head" style="left:661px;top:1016px">Follow &nbsp;Us</div>
<div class="f-row" style="left:661px;top:1047px">
  <span class="social" style="background:#3b5998" role="img" aria-label="Friendora"></span>
  <span class="social" style="background:#2aa3e0" role="img" aria-label="Chirplet"></span>
</div>
<div class="abs donate">A portion of all revenue<br>is donated to</div>
<div class="abs badge" style="left:661px" role="img" aria-label="Partner charity badge"></div>
<div class="abs badge" style="left:716px" role="img" aria-label="Partner charity badge"></div>

<div class="abs footer-bottom">Copyright © 2016 Dr. Mara J. Kalvoric. All Rights Reserved</div>

</body>
</html>
```